Real Estate Business Card

On the front side I want to have my info, my brokerage info.
On the back side I want have my complany’s logo, website and Facebook link. I will provide all this once I select a design.

I would like to see Black background and gold text, Dark Blue and gold text and White and blue text designs

Font styles to use
Sans Serif
Script

```html
<!DOCTYPE html>
<html lang="en">
<head>
<meta charset="utf-8">
<title>Stoutly Real Estate – Business Card</title>
<link rel="stylesheet" href="https://fonts.googleapis.com/css2?family=Montserrat:wght@700;800&family=Roboto:wght@400;500&display=swap">
<style>
  :root {
    --backdrop: #2b2b2d;
    --card: #1c1c1e;
    --brand-red: #d8343c;
    --gold: #ecd07a;
    --text-light: #f2f2f2;
    --mark-grey: #5d6170;
    --band: #7a83a0;
  }
  * { margin: 0; padding: 0; box-sizing: border-box; }
  html, body {
    width: 1200px; height: 900px; overflow: hidden;
    background: var(--backdrop);
  }
  .canvas { position: relative; width: 1200px; height: 900px; }
  .card {
    position: absolute; left: 250px; width: 700px; height: 400px;
    background: var(--card);
    overflow: hidden;
    box-shadow: 0 14px 30px rgba(0,0,0,0.45);
  }
  .card--back { top: 40px; }
  .card--front { top: 460px; }

  /* back side */
  .back-brand {
    position: absolute; right: 56px; bottom: 60px;
    display: flex; align-items: center; gap: 14px;
  }
  .back-brand__square { width: 34px; height: 34px; background: var(--brand-red); }
  .back-brand__name {
    font-family: "Montserrat", sans-serif; font-weight: 800;
    font-size: 44px; color: var(--brand-red); letter-spacing: 1px;
  }

  /* front side */
  .front-brand {
    position: absolute; left: 60px; top: 150px; width: 290px;
    font-family: "Montserrat", sans-serif; font-weight: 800;
    font-size: 44px; line-height: 1.05; color: var(--mark-grey);
  }
  .contact {
    position: absolute; left: 410px; top: 88px;
    font-family: "Roboto", sans-serif; color: var(--text-light);
    font-size: 19px; line-height: 1.3;
  }
  .contact__name {
    font-family: "Montserrat", sans-serif; font-weight: 800;
    font-size: 27px; color: var(--gold); letter-spacing: 0.5px; line-height: 1.05;
  }
  .contact__role {
    font-family: "Roboto", sans-serif; font-weight: 500;
    font-size: 19px; color: var(--brand-red); margin-bottom: 4px;
  }
  .contact__address { margin-bottom: 6px; }
  .contact__label { color: var(--gold); font-weight: 500; }

  .front-footer {
    position: absolute; left: 0; bottom: 0; width: 700px; height: 64px;
  }
  .website {
    position: absolute; left: 270px; bottom: 18px; width: 360px;
    text-align: center;
    font-family: "Roboto", sans-serif; font-weight: 500;
    font-size: 19px; letter-spacing: 2.5px; color: var(--text-light);
  }
</style>
</head>
<body>
<main class="canvas">
  <section class="card card--back" aria-label="Back side">
    <div class="back-brand">
      <span class="back-brand__square"></span>
      <span class="back-brand__name">STOUTLY</span>
    </div>
  </section>

  <section class="card card--front" aria-label="Front side">
    <div class="front-brand">STOUTLY REAL ESTATE</div>

    <div class="contact">
      <p class="contact__name">DALE HARROW</p>
      <p class="contact__role">CEO/FOUNDER</p>
      <p class="contact__address">4120 Birchwood Court<br>Juneau, Alaska 36120</p>
      <p><span class="contact__label">P:</span> 555 210 4471</p>
      <p><span class="contact__label">M:</span> 555 318 7092</p>
      <p><span class="contact__label">E:</span> dale@stoutlyhomes.com</p>
      <p><span class="contact__label">FB:</span> /stoutlyhomes</p>
    </div>

    <svg class="front-footer" viewBox="0 0 700 64" aria-hidden="true">
      <rect x="0" y="48" width="700" height="16" fill="var(--band)"/>
      <polygon points="290,4 610,4 630,64 270,64" fill="var(--brand-red)"/>
    </svg>
    <p class="website">www.stoutlyhomes.com</p>
  </section>
</main>
</body>
</html>
```